LIFE CHANGING NEW WEBSITE DESIGN NEEDED FOR FULL WEBSITE- FUN/FEMININE!

I need a website designed for a personal financial advice website geared at women called BLUE OTTER LANTERN. I will be providing free financial advice around topics of making, saving, spending and sharing money. The concept is to change the way women understand money and the necessity around building various passive income streams to ensure full financial freedom. This will then carry down to advice for mothers with children and children in particular. The website should be elegant and yet witty. I don't want lots of serious photos but more relatable. I will have a photo of myself and my story as this is a blog and needs to be relatable to women and mothers. I like pinks and greys. I want to have a pink piggy bank being broken with a hammer in the front screen to break our traditional mindset around piggy bank saving/spending habits. I have created a logo that is a pink piggy head with BLUE OTTER LANTERN that needs to be incorporated so that it blends into the heading. I have also already started designing the website on Squarespace and can provide access to that. Basically it should have a format of BLUE OTTER LANTERN LOGO center in header then on left hand navigation: MAKE, SAVE, SPEND, SHARE then on right hand header navigation: MISSION, GET STARTED, CONTACT BOL I would like to have the front page when you go to the url to have the image of the piggy bank being broken then a catchy phrase then under 4 boxes with MAKE (image and description) SAVE (image and description) SPEND (image and description) SHARE (image and description) if you click on those or the title they go to pages that are dedicated to each them. Each page should have a little intro on the topic then I want lots of blog links as I will be mainly writing blogs. Each blog site should have ability to write comments as well. I need social media icons on each page too. Please let me know what you need from me to get started. I prefer having a discussion if possible to not waste anyone's time. I need the site to be easy for me to use and add blogs/urls etc as needed. I also need the site to be put into my domain that I already purchased: www.blueotterlantern-sample.com

Target Market(s)

teenage girls, 20 something girls, 30 something girls and mothers

Coding

Coded - Design and coding required

Number of Pages Required

5+ page

Font styles to use
Sans Serif

Colors
e667a6
e34197
f59195
eea4c8
aaaaaa
cbcbcb
959595

Requirements
Must have
• TOP NAVIGATION
• MAKE SAVE SPEND SHARE LOGO/BLUE OTTER LANTERN MISSION GET STARTED CONTACT BOL
• FRONT PAGE: IMAGE OF PIGGY BANK BEING BROKEN WITH A HAMMER
• CATCH PHRASE OVER THE IMAGE
• BUTTON IN PINK- TAKE ACTION (WHICH DIRECTS TO TAKE ACTION TAB ON NAVIGATION HEADER
• 4 BOXES BELOW MAIN IMAGE WITH IMAGE/DESCRIPTIONS FOR MAKE, SAVE, SPEND, SHARE THAT EACH GO TO THE PAGES FROM THE NAVIGATION HEADER
• EACH PAGE SHOULD BE DEDICATED TO THOSE TOPICS THEN THERE IS AN INTRO ON EACH PAGE THEN THE LINKS TO DIFFERENT BLOGS AROUND EACH TOPIC FOR MAKE, SAVE, SPEND, SHARE
• EACH BLOG SHOULD HAVE COMMENTS SECTION AND SOCIAL MEDIA ICONS
• (GOOD TO USE PINKS/GREYS)
Should not have
• BE SUPER BUSY, CLUTTERED, FEEL LIKE I AM SELLING SOMETHING

```html
<!DOCTYPE html>
<html lang="en">
<head>
<meta charset="utf-8">
<title>Blue Otter Lantern</title>
<link rel="stylesheet" href="https://fonts.googleapis.com/css2?family=Comfortaa:wght@500&family=Rokkitt:wght@400;500&family=Noto+Serif:ital,wght@1,400&family=Lora:wght@400&display=swap">
<style>
  :root {
    --pink-brand: #e34197;
    --pink-soft: #eea4c8;
    --pink-button: #c2689c;
    --pink-accent: #c0679c;
    --grey-nav: #959595;
    --grey-hero: #e9e8e9;
    --ink: #222222;
    --sand: #d4b59b;
    --white: #ffffff;
  }
  * { margin: 0; padding: 0; box-sizing: border-box; }
  html, body { width: 1200px; height: 595px; overflow: hidden; background: var(--white); }
  .page { position: relative; width: 1200px; height: 595px; overflow: hidden; }

  .site-header { position: absolute; left: 0; top: 0; width: 1200px; height: 82px; background: var(--white); }
  .nav-link {
    position: absolute; top: 44px; transform: translateX(-50%);
    font-family: "Rokkitt", serif; font-size: 11px; color: var(--grey-nav);
    text-decoration: none; letter-spacing: 0.2px; white-space: nowrap;
  }
  .brand-mark {
    position: absolute; left: 585px; top: 6px; width: 30px; height: 30px;
    border-radius: 50%; background: var(--pink-soft);
  }
  .brand-name {
    position: absolute; left: 600px; top: 41px; transform: translateX(-50%);
    font-family: "Comfortaa", sans-serif; font-weight: 500; font-size: 18px;
    color: var(--pink-brand); white-space: nowrap;
  }

  .hero {
    position: absolute; left: 0; top: 82px; width: 1200px; height: 379px;
    background: radial-gradient(circle at 20% 60%, #f3f2f3 0%, var(--grey-hero) 55%, #dfdedf 100%);
  }
  .hero-visual {
    position: absolute; left: 580px; top: 0; width: 560px; height: 331px;
    background: radial-gradient(ellipse at 62% 78%, #f0a8bd 0%, #e7c0c9 30%, rgba(233,232,233,0) 62%),
                linear-gradient(155deg, rgba(233,232,233,0) 40%, rgba(200,160,120,0.35) 48%, rgba(233,232,233,0) 56%);
  }
  .hero-title {
    position: absolute; left: 290px; top: 82px;
    font-family: "Rokkitt", serif; font-weight: 500; font-size: 46px; color: var(--ink);
    letter-spacing: 0.5px; white-space: nowrap;
  }
  .hero-intro {
    position: absolute; left: 292px; top: 148px; width: 336px;
    font-family: "Lora", serif; font-size: 7.8px; line-height: 12.4px; color: var(--ink);
  }
  .hero-tagline {
    position: absolute; left: 292px; top: 224px;
    font-family: "Noto Serif", serif; font-style: italic; font-size: 12px; color: var(--ink);
  }
  .hero-tagline .highlight { color: var(--pink-accent); }
  .cta-button {
    position: absolute; left: 292px; top: 254px; width: 90px; height: 30px;
    background: var(--pink-button); color: var(--white);
    font-family: "Rokkitt", serif; font-weight: 500; font-size: 8.5px;
    display: flex; align-items: center; justify-content: center; text-decoration: none;
  }
  .promise-band {
    position: absolute; left: 125px; top: 331px; width: 950px; height: 48px;
    background: var(--sand); display: flex; align-items: center; justify-content: center;
    font-family: "Noto Serif", serif; font-style: italic; font-size: 11.5px; color: var(--white);
  }

  .topic-cards { position: absolute; left: 0; top: 508px; width: 1200px; height: 87px; }
  .topic-card {
    position: absolute; top: 0; width: 156px; height: 100px;
    border: 1px solid #f0f0f0; padding: 3px; background: var(--white);
  }
  .topic-image { width: 100%; height: 100%; }
  .card-make { left: 267px; }
  .card-make .topic-image { background: linear-gradient(120deg, #ece6e1 0%, #d9c7b4 45%, #8c3a3f 100%); }
  .card-save { left: 437px; }
  .card-save .topic-image { background: radial-gradient(ellipse at 80% 70%, #f2a8cc 0%, #f7d6e6 35%, #ffffff 65%); }
  .card-spend { left: 607px; }
  .card-spend .topic-image { background: linear-gradient(110deg, #e6e6e6 0%, #d8d8d5 55%, #b8c2a9 72%, #c23a2e 100%); }
  .card-share { left: 777px; }
  .card-share .topic-image { background: linear-gradient(180deg, #efeae4 0%, #e2d6c4 55%, #c99a7a 100%); }
</style>
</head>
<body>
<div class="page">
  <header class="site-header">
    <a class="nav-link" href="#" style="left:329px">Make</a>
    <a class="nav-link" href="#" style="left:375px">Save</a>
    <a class="nav-link" href="#" style="left:423px">Spend</a>
    <a class="nav-link" href="#" style="left:474px">Share</a>
    <span class="brand-mark"></span>
    <span class="brand-name">Blue Otter Lantern</span>
    <a class="nav-link" href="#" style="left:730px">Mission</a>
    <a class="nav-link" href="#" style="left:797px">Get Started</a>
    <a class="nav-link" href="#" style="left:872px">Contact Me</a>
  </header>

  <section class="hero">
    <div class="hero-visual" role="img" aria-label="Hammer striking a pink piggy bank that breaks open spilling banknotes"></div>
    <h1 class="hero-title">Expert Money Coach</h1>
    <p class="hero-intro">Empowering you to eliminate obstacles, gain clarity, set goals and holds you accountable to achieve your desires. If you're feeling stuck, confused or unhappy about your finances, Blue Otter Lantern provides you with the tools to take action.</p>
    <p class="hero-tagline">Obtain <span class="highlight">Finacial</span> Freedom Today</p>
    <a class="cta-button" href="#">Start Now</a>
    <div class="promise-band">Empower yourself within months to achieve everything you want in life</div>
  </section>

  <section class="topic-cards">
    <article class="topic-card card-make"><div class="topic-image" role="img" aria-label="Woman working at a desk at home"></div></article>
    <article class="topic-card card-save"><div class="topic-image" role="img" aria-label="Pink piggy bank on white"></div></article>
    <article class="topic-card card-spend"><div class="topic-image" role="img" aria-label="Banknotes and coins spilling from a red wallet on marble"></div></article>
    <article class="topic-card card-share"><div class="topic-image" role="img" aria-label="Friends in sun hats laughing together on a beach"></div></article>
  </section>
</div>
</body>
</html>
```